BOLD & MINIMALIST DESIGN NEEDED

We want a very bold but minimalistic business card design that is impactful and utilizes both sides of the business card. Our current logo is included for your use.

We want bold fonts and good use of negative space. We don't want the logo to overpower the design.

Target Market(s)

Professionals who are building new commercial buildings.

Industry/Entity Type

Construction

Contact Information for Business Card

Name, Title, email, office phone, cell phone, website

Font styles to use
Serif
Sans Serif

Requirements
Must have
• Bold design!

```html
<!DOCTYPE html>
<html lang="en">
<head>
<meta charset="UTF-8">
<title>Ridgeway Design + Build — Business Card</title>
<link href="https://fonts.googleapis.com/css2?family=Open+Sans:wght@400;600;800&display=swap" rel="stylesheet">
<style>
  :root {
    --page-bg: #ececec;
    --card-white: #ffffff;
    --card-black: #0b0b0b;
    --card-black-soft: #1c1c1c;
    --ink: #111111;
    --ink-soft: #6a6a6a;
    --accent-green: #6cbd35;
    --rule: #9a9a9a;
  }
  * { box-sizing: border-box; margin: 0; padding: 0; }
  html, body {
    width: 1200px; height: 900px; overflow: hidden;
    background: var(--page-bg);
    font-family: "Open Sans", Arial, sans-serif;
  }
  .stage {
    position: relative; width: 1200px; height: 900px;
    display: flex; align-items: center; justify-content: center; gap: 50px;
  }
  .card {
    width: 520px; height: 300px; border-radius: 26px;
    position: relative; overflow: hidden;
    box-shadow: 0 10px 28px rgba(0,0,0,0.18);
  }
  .card-front { background: var(--card-white); }
  .card-back {
    background: radial-gradient(ellipse at 60% 35%, var(--card-black-soft) 0%, var(--card-black) 70%);
    display: flex; align-items: center; justify-content: center;
  }

  /* Front: brand block */
  .brand {
    position: absolute; left: 34px; top: 0; bottom: 0; width: 210px;
    display: flex; align-items: center; gap: 10px;
  }
  .brand-mark { width: 16px; height: 16px; background: var(--accent-green); flex: none; }
  .brand-name {
    font-weight: 800; font-size: 22px; line-height: 1.1; color: var(--ink);
    text-transform: uppercase; letter-spacing: 0.5px;
  }
  .divider {
    position: absolute; left: 258px; top: 48px; bottom: 48px;
    width: 1px; background: var(--rule);
  }

  /* Front: contact block */
  .contact {
    position: absolute; left: 282px; top: 58px; right: 20px;
    color: var(--ink-soft);
  }
  .person-name {
    font-weight: 600; font-size: 22px; color: var(--accent-green);
    text-transform: uppercase; letter-spacing: 0.3px; line-height: 1.1;
  }
  .person-title { font-size: 15px; margin-top: 2px; }
  .address { font-size: 15px; line-height: 1.35; margin-top: 12px; }
  .contact-list { list-style: none; margin-top: 12px; font-size: 15px; line-height: 1.45; }
  .contact-list li { display: flex; align-items: center; gap: 7px; }
  .contact-icon { width: 12px; height: 12px; flex: none; }

  /* Back */
  .back-name {
    font-weight: 800; font-size: 34px; color: #ffffff;
    text-transform: uppercase; letter-spacing: 1px; text-align: center; line-height: 1.15;
  }
</style>
</head>
<body>
<main class="stage">
  <section class="card card-front" aria-label="Card front">
    <div class="brand">
      <span class="brand-mark"></span>
      <span class="brand-name">Ridgeway Design + Build</span>
    </div>
    <div class="divider"></div>
    <div class="contact">
      <p class="person-name">Jonathan Smith</p>
      <p class="person-title">Managing Director</p>
      <p class="address">Your Address, City<br>State, Zip 0000</p>
      <ul class="contact-list">
        <li>
          <svg class="contact-icon" viewBox="0 0 12 12" aria-hidden="true"><path d="M2 1h2.5l1 2.5-1.5 1a6 6 0 0 0 3.5 3.5l1-1.5 2.5 1V10a1 1 0 0 1-1 1A9 9 0 0 1 1 2a1 1 0 0 1 1-1z" fill="var(--accent-green)"/></svg>
          044-123 456 789
        </li>
        <li>
          <svg class="contact-icon" viewBox="0 0 12 12" aria-hidden="true"><rect x="0.5" y="2" width="11" height="8" rx="1" fill="var(--accent-green)"/><path d="M1 2.5l5 4 5-4" stroke="#fff" stroke-width="1" fill="none"/></svg>
          info@webname.com
        </li>
        <li>
          <svg class="contact-icon" viewBox="0 0 12 12" aria-hidden="true"><circle cx="6" cy="6" r="5.5" fill="var(--accent-green)"/><path d="M0.5 6h11M6 0.5c-2.5 3-2.5 8 0 11M6 0.5c2.5 3 2.5 8 0 11" stroke="#fff" stroke-width="0.8" fill="none"/></svg>
          www.websitename.com
        </li>
      </ul>
    </div>
  </section>

  <section class="card card-back" aria-label="Card back">
    <p class="back-name">Ridgeway<br>Design + Build</p>
  </section>
</main>
</body>
</html>
```